Business cards for KORU Real Estate Holdings LLC

We need a cool, original business card design for a company based in the Washington DC metropolitan area. We are a new energetic and passionate Real Estate Investing Company that invests in all types of real estate; commercial, residential, industrial etc.

Our company color is Red since it reflects action, energy and speed; it is assertive confident, energizing, exciting, powerful, passionate and determined. So we would like business card communicate those qualities to the audience.

Our audiences are investors that want to invest with us, real estate sellers, buyers, and tenants who lease from us.

Our logo is attached

```html
<!DOCTYPE html>
<html lang="en">
<head>
<meta charset="utf-8">
<title>KORU Real Estate Holdings LLC – Business Card</title>
<link rel="stylesheet" href="https://fonts.googleapis.com/css2?family=Montserrat:wght@400;600;800&display=swap">
<style>
  :root {
    --page-bg: #cfccc7;
    --card-bg: #ecebe8;
    --band-dark: #4a4a4c;
    --brand-red: #d8333a;
    --ink: #3a3a3c;
    --ink-soft: #55555a;
  }
  * { margin: 0; padding: 0; box-sizing: border-box; }
  html, body {
    width: 1200px; height: 763px; overflow: hidden;
    background: var(--page-bg);
    font-family: "Montserrat", Arial, sans-serif;
  }
  .card {
    position: absolute; left: 80px; top: 84px;
    width: 1040px; height: 594px;
    background: var(--card-bg);
    border-radius: 34px;
    overflow: hidden;
    box-shadow: 0 10px 30px rgba(0,0,0,.18);
  }
  .card-accent {
    position: absolute; left: 0; top: 0;
    width: 210px; height: 100%;
    background: linear-gradient(180deg, var(--band-dark) 0%, var(--band-dark) 55%, #7a3a3d 80%, var(--brand-red) 100%);
  }
  .brand { position: absolute; left: 270px; top: 222px; display: flex; align-items: center; gap: 20px; }
  .brand-dot { width: 62px; height: 62px; border-radius: 50%; background: var(--brand-red); }
  .brand-name { font-weight: 800; font-size: 96px; line-height: 1; color: var(--ink); letter-spacing: 2px; }
  .person { position: absolute; left: 258px; top: 362px; color: var(--ink); }
  .person-name { font-size: 32px; font-weight: 400; line-height: 1.1; }
  .person-name strong { font-weight: 600; }
  .person-title { font-size: 22px; color: var(--ink-soft); margin-top: 8px; }
  .contact { position: absolute; left: 719px; top: 360px; color: var(--ink); font-size: 25px; line-height: 35px; }
  .contact-list { list-style: none; margin-top: 10px; font-size: 23px; }
  .contact-list li { display: flex; align-items: center; gap: 14px; height: 35px; }
  .contact-icon { width: 22px; height: 22px; flex: none; }
</style>
</head>
<body>
  <main class="card">
    <div class="card-accent" role="img" aria-label="Decorative dark grey and red swoosh band along the left edge"></div>

    <div class="brand">
      <span class="brand-dot"></span>
      <span class="brand-name">KORU</span>
    </div>

    <div class="person">
      <p class="person-name"><strong>Daniel</strong> Reyes</p>
      <p class="person-title">Owner / C.E.O.</p>
    </div>

    <div class="contact">
      <p class="contact-address">Harbor Street 2210<br>DC Suite # 3107</p>
      <ul class="contact-list">
        <li>
          <svg class="contact-icon" viewBox="0 0 24 24" aria-hidden="true"><circle cx="12" cy="12" r="12" fill="var(--ink)"/><path d="M8 6 L10 6 L11 9 L9.5 10.5 C10.5 12.5 11.5 13.5 13.5 14.5 L15 13 L18 14 L18 16 C18 17 17 18 16 18 C10.5 17.5 6.5 13.5 6 8 C6 7 7 6 8 6 Z" fill="var(--card-bg)"/></svg>
          202-555-0147
        </li>
        <li>
          <svg class="contact-icon" viewBox="0 0 24 24" aria-hidden="true"><circle cx="12" cy="12" r="12" fill="var(--ink)"/><path d="M8 6 L10 6 L11 9 L9.5 10.5 C10.5 12.5 11.5 13.5 13.5 14.5 L15 13 L18 14 L18 16 C18 17 17 18 16 18 C10.5 17.5 6.5 13.5 6 8 C6 7 7 6 8 6 Z" fill="var(--card-bg)"/></svg>
          202-555-0183
        </li>
        <li>
          <svg class="contact-icon" viewBox="0 0 24 24" aria-hidden="true"><circle cx="12" cy="12" r="12" fill="var(--ink)"/><rect x="8.5" y="5.5" width="7" height="13" rx="1.5" fill="var(--card-bg)"/><rect x="9.8" y="7.5" width="4.4" height="8" fill="var(--ink)"/></svg>
          202-555-0129
        </li>
        <li>
          <svg class="contact-icon" viewBox="0 0 24 24" aria-hidden="true"><rect x="2" y="5" width="20" height="14" rx="2" fill="var(--ink)"/><path d="M3 6.5 L12 13 L21 6.5" fill="none" stroke="var(--card-bg)" stroke-width="1.6"/></svg>
          info@korure.com
        </li>
      </ul>
    </div>
  </main>
</body>
</html>
```